Local Roofing/Construction company business needs new biz card design

We need a new business card design, current cards are from the start of this operation and generic at best. We are a local Construction Company (General Contractor) with a majority of our work originating from insurance claims-exterior finish work is the main focus (Roofs-Siding-Gutters etc). Heavily involved with homeowners and the low ball offers they receive from insurance company's after a insurable event takes place. I have attached some of our original logo file(s) below.

```html
<!DOCTYPE html>
<html lang="en">
<head>
<meta charset="utf-8">
<title>Stonebridge Construction – Business Card</title>
<link rel="stylesheet" href="https://fonts.googleapis.com/css2?family=Lato:wght@400;700;900&display=swap">
<style>
  :root {
    --stage: #232527;
    --card-dark: #0d1e22;
    --brand-green: #22dd77;
    --rule-white: #e8ecea;
    --text-light: #e6ecea;
  }
  * { margin: 0; padding: 0; box-sizing: border-box; }
  html, body { width: 1200px; height: 952px; overflow: hidden; }
  body {
    background: var(--stage);
    font-family: "Lato", sans-serif;
    display: flex;
    align-items: center;
    justify-content: center;
    gap: 40px;
  }
  .card {
    position: relative;
    width: 540px;
    height: 308px;
    border-radius: 22px;
    overflow: hidden;
  }
  .card--front { background: var(--card-dark); }
  .card--back { background: var(--brand-green); }
  .card-edge {
    position: absolute;
    left: 0; bottom: 0;
    width: 100%; height: 30px;
  }

  /* front */
  .front-brand {
    position: absolute;
    left: 40px; top: 52px;
    width: 200px; height: 180px;
    display: flex; flex-direction: column;
    justify-content: center; align-items: flex-start;
    gap: 10px;
  }
  .brand-square {
    width: 34px; height: 34px;
    background: var(--brand-green);
    border-radius: 4px;
  }
  .brand-name {
    font-weight: 900;
    font-size: 26px;
    line-height: 1.05;
    letter-spacing: 0.5px;
    text-transform: uppercase;
    color: var(--brand-green);
  }
  .contact-block {
    position: absolute;
    left: 262px; top: 62px;
    color: var(--text-light);
  }
  .person-name {
    font-size: 19px;
    letter-spacing: 0.5px;
    text-transform: uppercase;
    color: var(--brand-green);
    font-weight: 400;
  }
  .person-name strong { font-weight: 900; }
  .person-title { font-size: 14px; margin-top: 2px; }
  .contact-list { list-style: none; margin-top: 14px; }
  .contact-item {
    display: flex; align-items: flex-start; gap: 8px;
    font-size: 12.5px; line-height: 1.35;
    margin-bottom: 7px;
  }
  .contact-icon { flex: none; width: 17px; height: 17px; margin-top: 0; }

  /* back */
  .back-brand {
    position: absolute;
    left: 50%; top: 44%;
    transform: translate(-50%, -50%);
    display: flex; align-items: center; gap: 14px;
  }
  .back-brand .brand-square { background: var(--card-dark); width: 40px; height: 40px; }
  .back-brand .brand-name { color: var(--card-dark); font-size: 32px; }
</style>
</head>
<body>

  <section class="card card--front" aria-label="Business card front">
    <div class="front-brand">
      <span class="brand-square"></span>
      <span class="brand-name">Stonebridge<br>Construction</span>
    </div>

    <div class="contact-block">
      <h1 class="person-name">Daniel M. <strong>Hartley</strong></h1>
      <p class="person-title">General Contractor</p>
      <ul class="contact-list">
        <li class="contact-item">
          <svg class="contact-icon" viewBox="0 0 17 17"><rect width="17" height="17" rx="3" fill="#22dd77"/><path d="M8.5 3.2a3.6 3.6 0 0 0-3.6 3.6c0 2.7 3.6 6.8 3.6 6.8s3.6-4.1 3.6-6.8a3.6 3.6 0 0 0-3.6-3.6z" fill="#0d1e22"/><circle cx="8.5" cy="6.8" r="1.3" fill="#22dd77"/></svg>
          <span>1720 Linden Park Avenue<br>Riverton, OH 45012</span>
        </li>
        <li class="contact-item">
          <svg class="contact-icon" viewBox="0 0 17 17"><rect width="17" height="17" rx="3" fill="#e6ecea"/><path d="M5 3.5l2 .2.9 2.4-1.3 1a6 6 0 0 0 2.8 2.8l1-1.3 2.4.9.2 2c-.3.8-1 1.2-1.8 1.1A8.5 8.5 0 0 1 3.9 5.3c-.1-.8.3-1.5 1.1-1.8z" fill="#0d1e22"/></svg>
          <span>+00 555 201 48</span>
        </li>
        <li class="contact-item">
          <svg class="contact-icon" viewBox="0 0 17 17"><rect width="17" height="17" rx="3" fill="#e6ecea"/><rect x="3.5" y="5" width="10" height="7" fill="none" stroke="#0d1e22" stroke-width="1.4"/><path d="M3.5 5l5 4 5-4M3.5 12l4-3.5M13.5 12l-4-3.5" fill="none" stroke="#0d1e22" stroke-width="1.2"/></svg>
          <span>hello@stonebridgebuild.com</span>
        </li>
        <li class="contact-item">
          <svg class="contact-icon" viewBox="0 0 17 17"><rect width="17" height="17" rx="3" fill="#e6ecea"/><path d="M5 3.5l7.5 6-3.3.3 1.9 3.7-1.4.7-1.9-3.7L5 13z" fill="#0d1e22"/></svg>
          <span>www.stonebridgebuild.com</span>
        </li>
      </ul>
    </div>

    <svg class="card-edge" viewBox="0 0 540 30" preserveAspectRatio="none" aria-hidden="true">
      <rect x="0" y="17" width="262" height="3" fill="#e8ecea"/>
      <polygon points="262,17 540,17 540,30 274,30 262,20" fill="#22dd77"/>
    </svg>
  </section>

  <section class="card card--back" aria-label="Business card back">
    <div class="back-brand">
      <span class="brand-square"></span>
      <span class="brand-name">Stonebridge<br>Construction</span>
    </div>
    <svg class="card-edge" viewBox="0 0 540 30" preserveAspectRatio="none" aria-hidden="true">
      <rect x="0" y="17" width="262" height="3" fill="#e8ecea"/>
      <polygon points="262,17 540,17 540,30 274,30 262,20" fill="#0d1e22"/>
    </svg>
  </section>

</body>
</html>
```